Business Card Design For Office Furniture Clearance Company

Kestrel Office Clearance - our company name pretty much explains what we do, we clear offices for high end clients, mainly plc's and large international companies.

We require a nice looking business card that displays professionalism but without being too serious.

It would be nice to see just a little more than a conventional boring business card, make sure you add some flare.

Industry/Entity Type

Office Furniture

Contact Information for Business Card

CARD 1

Mark Holloway
Director
mark@kestrelofficeclearance.co.uk
m: 07700 153928

t: 01632 960418
www.kestrelofficeclearance.co.uk

Kestrel Office Clearance
Unit K4 B
2-8 Fenwick Lane
Harwick
Elmsford Vale
ZZ9 4QT

free office clearances… you cant get better than that.

CARD 2

Peter Radford
Director
peter@kestrelofficeclearance.co.uk
m: 07700 382615

t: 01632 960418

Kestrel Office Clearance
Unit K4 B
2-8 Fenwick Lane
Harwick
Elmsford Vale
ZZ9 4QT

Font styles to use
Sans Serif

Requirements
Must have
• A white background - as we have a blue logo.
Nice to have
• Nice use of the logo - play around with this and dissect it.

```html
<!DOCTYPE html>
<html lang="en">
<head>
<meta charset="utf-8">
<title>Kestrel Office Clearance – Business Cards</title>
<link rel="stylesheet" href="https://fonts.googleapis.com/css2?family=Montserrat:wght@400;500;700&display=swap">
<style>
  :root {
    --blue: #1f7fc0;
    --blue-deep: #1a64a0;
    --navy: #16528c;
    --white: #ffffff;
    --backdrop: #e9ecef;
    --text: #1d6fb3;
  }
  * { box-sizing: border-box; margin: 0; padding: 0; }
  html, body {
    width: 1200px; height: 900px; overflow: hidden;
    background: var(--backdrop);
    font-family: "Montserrat", sans-serif;
  }
  .canvas { position: relative; width: 1200px; height: 900px; }

  .card {
    position: absolute;
    width: 640px; height: 380px;
    background: var(--white);
    border-radius: 26px;
    overflow: hidden;
    box-shadow: 0 10px 30px rgba(20, 40, 70, 0.18);
  }
  .card--front { left: 80px; top: 50px; }
  .card--back  { left: 480px; top: 470px; }

  /* brand lockup: plain circle + name */
  .brand {
    position: absolute;
    display: flex; align-items: center; gap: 22px;
  }
  .brand__dot {
    flex: none;
    border-radius: 50%;
    background: var(--blue);
  }
  .brand__name {
    color: var(--blue);
    font-weight: 700;
    line-height: 1.1;
    text-transform: uppercase;
    letter-spacing: 0.02em;
  }

  .card--front .brand { left: 110px; top: 95px; }
  .card--front .brand__dot { width: 150px; height: 150px; }
  .card--front .brand__name { font-size: 30px; width: 230px; }

  .tagline-band {
    position: absolute; left: 0; right: 0; bottom: 0;
    height: 34px;
    background: var(--blue-deep);
    color: var(--white);
    font-size: 15px; font-weight: 500;
    letter-spacing: 0.06em;
    text-transform: uppercase;
    display: flex; align-items: center; justify-content: flex-end;
    padding-right: 34px;
  }

  /* back card */
  .side-strip { position: absolute; left: 0; top: 0; width: 60px; height: 380px; }

  .details {
    position: absolute; left: 78px; top: 44px;
    color: var(--text);
  }
  .details__company {
    font-size: 19px; font-weight: 700; color: var(--navy);
    letter-spacing: 0.03em; text-transform: uppercase;
    margin-bottom: 20px;
  }
  .details__name {
    font-size: 21px; font-weight: 700; color: var(--navy);
    text-transform: uppercase; letter-spacing: 0.01em;
  }
  .details__role {
    font-size: 14px; font-weight: 400; text-transform: uppercase;
    margin-bottom: 8px;
  }
  .address { font-style: normal; font-size: 15px; line-height: 1.28; margin-bottom: 8px; }
  .contact-list { list-style: none; font-size: 15px; line-height: 1.35; }
  .contact-list li { display: flex; align-items: center; gap: 9px; }
  .contact-list svg { width: 13px; height: 13px; flex: none; }

  .card--back .brand { right: 40px; top: 40px; flex-direction: column; gap: 14px; }
  .card--back .brand__dot { width: 190px; height: 190px; }
  .card--back .brand__name { font-size: 20px; text-align: center; width: 220px; }
</style>
</head>
<body>
<main class="canvas">

  <section class="card card--front" aria-label="Business card front">
    <div class="brand">
      <span class="brand__dot"></span>
      <span class="brand__name">Kestrel Office Clearance</span>
    </div>
    <div class="tagline-band">Free office clearances... you cant get better than that</div>
  </section>

  <section class="card card--back" aria-label="Business card back">
    <svg class="side-strip" viewBox="0 0 60 380" aria-hidden="true">
      <rect x="0" y="0" width="34" height="380" fill="var(--blue)"/>
      <polygon points="0,250 34,215 60,228 60,380 0,380" fill="var(--blue-deep)"/>
      <line x1="0" y1="250" x2="34" y2="215" stroke="var(--white)" stroke-width="3"/>
      <line x1="34" y1="215" x2="60" y2="228" stroke="var(--white)" stroke-width="3"/>
    </svg>

    <div class="details">
      <p class="details__company">Kestrel Office Clearance</p>
      <p class="details__name">Mark Holloway</p>
      <p class="details__role">Director</p>
      <address class="address">
        Kestrel Office Clearance<br>
        Unit K4 B<br>
        2-8 Fenwick Lane<br>
        Harwick<br>
        Elmsford Vale<br>
        ZZ9 4QT
      </address>
      <ul class="contact-list">
        <li>
          <svg viewBox="0 0 16 16" aria-hidden="true"><rect x="4" y="1" width="8" height="14" rx="1.5" fill="none" stroke="currentColor" stroke-width="1.6"/><circle cx="8" cy="12.3" r="0.9" fill="currentColor"/></svg>
          07700 153928
        </li>
        <li>
          <svg viewBox="0 0 16 16" aria-hidden="true"><path d="M4 1.5 6.5 5 5 6.5c1 2 2.5 3.5 4.5 4.5L11 9.5l3.5 2.5-1.5 2.5C7.5 14 2 8.5 1.5 3z" fill="currentColor"/></svg>
          01632 960418
        </li>
        <li>
          <svg viewBox="0 0 16 16" aria-hidden="true"><rect x="1.5" y="3.5" width="13" height="9" rx="1" fill="none" stroke="currentColor" stroke-width="1.5"/><path d="M2 4l6 5 6-5" fill="none" stroke="currentColor" stroke-width="1.5"/></svg>
          mark@kestrelofficeclearance.co.uk
        </li>
        <li>
          <svg viewBox="0 0 16 16" aria-hidden="true"><circle cx="8" cy="8" r="6.5" fill="none" stroke="currentColor" stroke-width="1.4"/><ellipse cx="8" cy="8" rx="2.8" ry="6.5" fill="none" stroke="currentColor" stroke-width="1.2"/><line x1="1.5" y1="8" x2="14.5" y2="8" stroke="currentColor" stroke-width="1.2"/></svg>
          www.kestrelofficeclearance.co.uk
        </li>
      </ul>
    </div>

    <div class="brand">
      <span class="brand__dot"></span>
      <span class="brand__name">Kestrel Office Clearance</span>
    </div>
  </section>

</main>
</body>
</html>
```